Professional, modern and unique business card. We are looking to present a new look to our business cards however we don't want to divert too far away from original template. We want social media links and our 3 office addresses on the backside of the business cards. Please see attached business card templates for ideas.
Crestline Homes Color Code:
R: 7
G:63
B:86

Target Market(s)

Real Estate

Industry/Entity Type

Real Estate

Contact Information for Business Card

Follow the attached templates. In need of a more modern and unique touch but don't want to divert from the original theme or color.
Crestline Homes Color Code:
R: 7
G:63
B:86

Font styles to use
Serif

Requirements
Must have
• Crestline Homes logo, Crestline homes colors, social media links, 3 office addresses,
Nice to have
• information about Crestline Homes and QR codes. You can check out www.mycrestlinehomes.example

```html
<!DOCTYPE html>
<html lang="en">
<head>
<meta charset="utf-8">
<title>Crestline Homes – Business Card</title>
<link href="https://fonts.googleapis.com/css2?family=Lato:wght@400;700&display=swap" rel="stylesheet">
<style>
  :root {
    --stage: #e6e8ea;
    --card-blue: #0f78b1;
    --card-blue-back: #1680b8;
    --ink: #ffffff;
    --ink-soft: rgba(255,255,255,0.85);
    --rule: rgba(255,255,255,0.45);
    --shadow: rgba(0,0,0,0.22);
  }
  * { box-sizing: border-box; margin: 0; padding: 0; }
  html, body { width: 1200px; height: 782px; overflow: hidden; }
  body {
    background: var(--stage);
    font-family: "Lato", Arial, sans-serif;
    color: var(--ink);
    position: relative;
  }
  .card {
    position: absolute;
    width: 620px;
    height: 354px;
    box-shadow: 0 10px 24px var(--shadow);
  }
  /* ---------- back side ---------- */
  .card--back {
    left: 470px; top: 36px;
    background: var(--card-blue-back);
  }
  .social {
    position: absolute;
    list-style: none;
    display: flex; flex-direction: column; gap: 12px;
    font-size: 17px;
  }
  .social--left { left: 40px; top: 46px; }
  .social--right { left: 380px; top: 130px; }
  .social li { display: flex; align-items: center; gap: 9px; }
  .social .dot {
    width: 20px; height: 20px; border-radius: 50%;
    background: var(--ink); flex: none;
  }
  .offices {
    position: absolute; left: 40px; right: 40px; bottom: 40px;
    display: flex; justify-content: space-between;
    border-top: 1px solid var(--rule);
    padding-top: 16px;
    font-size: 16px; line-height: 1.25;
  }
  .office { padding: 0 14px; font-style: normal; }
  .office:first-child { padding-left: 0; }
  .office:last-child { padding-right: 0; }
  .office + .office { border-left: 1px solid var(--rule); }
  /* ---------- front side ---------- */
  .card--front {
    left: 170px; top: 392px;
    background: var(--card-blue);
  }
  .brand {
    position: absolute; left: 40px; top: 0; bottom: 0; width: 250px;
    display: flex; align-items: center; gap: 12px;
  }
  .brand-mark {
    width: 34px; height: 34px; border-radius: 50%;
    background: var(--ink); flex: none;
  }
  .brand-name {
    font-weight: 700; font-size: 27px; line-height: 1.05;
    letter-spacing: 1px; text-transform: uppercase;
  }
  .divider {
    position: absolute; left: 300px; top: 60px; bottom: 60px;
    width: 1px; background: var(--rule);
  }
  .person { position: absolute; left: 330px; top: 82px; }
  .person-name { font-weight: 700; font-size: 24px; letter-spacing: 0.5px; }
  .person-role { font-size: 16px; letter-spacing: 1px; color: var(--ink-soft); margin-top: 2px; }
  .contacts {
    list-style: none; margin-top: 16px;
    display: flex; flex-direction: column; gap: 4px;
    font-size: 16px;
  }
  .contacts li { display: flex; align-items: center; gap: 8px; }
  .contacts svg { width: 13px; height: 13px; flex: none; fill: var(--ink); }
</style>
</head>
<body>

  <section class="card card--back" aria-label="Back of business card">
    <ul class="social social--left">
      <li><span class="dot"></span>CrestlineHomesNY</li>
      <li><span class="dot"></span>Info at Crestline Homes</li>
      <li><span class="dot"></span>Crestline Homes New York</li>
    </ul>
    <ul class="social social--right">
      <li><span class="dot"></span>Crestline Homes</li>
      <li><span class="dot"></span>@CrestlineHomesQ</li>
      <li><span class="dot"></span>@CrestlineHomesNY</li>
    </ul>
    <div class="offices">
      <address class="office">140-12 Harbor Blvd<br>Bayview, NY 11290</address>
      <address class="office">72-30 Maple Blvd<br>Elm Garden, NY 11488</address>
      <address class="office">905 Cedar Ave<br>Riverside, NY 11277</address>
    </div>
  </section>

  <section class="card card--front" aria-label="Front of business card">
    <div class="brand">
      <span class="brand-mark"></span>
      <span class="brand-name">Crestline<br>Homes</span>
    </div>
    <div class="divider"></div>
    <div class="person">
      <div class="person-name">LORUM SMITH</div>
      <div class="person-role">MANAGING DIRECTOR</div>
      <ul class="contacts">
        <li><svg viewBox="0 0 16 16" aria-hidden="true"><path d="M3 1h3l1 4-2 1a9 9 0 0 0 5 5l1-2 4 1v3a2 2 0 0 1-2 2A13 13 0 0 1 1 3a2 2 0 0 1 2-2z"/></svg>212 555 0147</li>
        <li><svg viewBox="0 0 16 16" aria-hidden="true"><path d="M4 0h8a1 1 0 0 1 1 1v14a1 1 0 0 1-1 1H4a1 1 0 0 1-1-1V1a1 1 0 0 1 1-1zm1 2v10h6V2zm3 11a1 1 0 1 0 0 2 1 1 0 0 0 0-2z"/></svg>917 555 0263</li>
        <li><svg viewBox="0 0 16 16" aria-hidden="true"><path d="M4 1h8v4h2a1 1 0 0 1 1 1v6h-3v3H4v-3H1V6a1 1 0 0 1 1-1h2zm1 1v3h6V2zm0 9v3h6v-3z"/></svg>718 555 0390</li>
        <li><svg viewBox="0 0 16 16" aria-hidden="true"><path d="M1 3h14v10H1zm1 1v.5l6 4 6-4V4z"/></svg>info@crestlinehomes.example</li>
        <li><svg viewBox="0 0 16 16" aria-hidden="true"><circle cx="8" cy="8" r="7"/></svg>www.mycrestlinehomes.example</li>
      </ul>
    </div>
  </section>

</body>
</html>
```